Business Card for beauty technology startup

Design Glimora Business Card for a Beauty, based on the website identity and colors (https://www.glimora-example.com).
Glimora is a beauty tech startup that gathers helpful product info for beauty lovers and consumers (such as availability on stores, price range and product reviews) for makeup products. The card design must be young, colorful but clean, and very modern.

Target Market(s)

woman, 15-35

Industry/Entity Type

Cosmetics

Contact Information for Business Card

Full Name, address, phone

Font styles to use
Other font styles liked:
• Advent Pro

Colors
e34297
86cfc6
ffffff
5c5c5c
e8e8e8
e667a6
b2b2b2

Requirements
Must have
• One full colored side with a creative design and another with card info
• Use Color palette: #95C5C5 and/or #D38AA5
• Use fonts: Advent Pro
• Use website identity: https://www.glimora-example.com
Nice to have
• If needed extra font: Roboto

```html
<!DOCTYPE html>
<html lang="en">
<head>
<meta charset="UTF-8">
<title>Glimora Business Card</title>
<link rel="stylesheet" href="https://fonts.googleapis.com/css2?family=Advent+Pro:wght@300;400;500;600&family=Roboto:wght@400&display=swap">
<style>
  :root {
    --backdrop: #3b3b3d;
    --card: #1e1c20;
    --card-edge: #2a282c;
    --emboss: #3d3c42;
    --rose: #b0738b;
    --teal: #8ccfc6;
    --muted: #b8748e;
  }
  * { box-sizing: border-box; margin: 0; padding: 0; }
  html, body {
    width: 799px;
    height: 1200px;
    overflow: hidden;
    background: var(--backdrop);
  }
  .canvas {
    position: relative;
    width: 799px;
    height: 1200px;
  }
  .card {
    position: absolute;
    left: 80px;
    width: 640px;
    height: 366px;
    background: var(--card);
    border: 1px solid var(--card-edge);
    border-radius: 4px;
    box-shadow: 0 18px 40px rgba(0,0,0,0.45);
    overflow: hidden;
  }
  .card--front { top: 130px; }
  .card--back  { top: 704px; }

  /* Front */
  .front-mark {
    position: absolute;
    inset: 0;
    display: flex;
    align-items: center;
    justify-content: center;
    gap: 16px;
  }
  .front-mark__dot {
    width: 16px;
    height: 16px;
    border-radius: 50%;
    background: var(--emboss);
  }
  .front-mark__name {
    font-family: "Advent Pro", sans-serif;
    font-weight: 500;
    font-size: 64px;
    letter-spacing: 2px;
    color: var(--emboss);
  }

  /* Back */
  .back-wordmark {
    position: absolute;
    left: 34px;
    top: 26px;
    font-family: "Advent Pro", sans-serif;
    font-weight: 300;
    font-size: 46px;
    letter-spacing: 11px;
    color: var(--rose);
    text-transform: uppercase;
  }
  .contact {
    position: absolute;
    left: 34px;
    top: 128px;
    font-family: "Roboto", sans-serif;
    color: var(--muted);
  }
  .contact__name {
    font-family: "Advent Pro", sans-serif;
    font-weight: 600;
    font-size: 25px;
    letter-spacing: 0.5px;
    color: var(--teal);
    text-transform: uppercase;
    margin-bottom: 8px;
  }
  .contact__address {
    font-size: 15px;
    line-height: 20px;
    margin-bottom: 6px;
  }
  .contact__list { list-style: none; }
  .contact__item {
    display: flex;
    align-items: center;
    gap: 10px;
    font-size: 15px;
    line-height: 22px;
  }
  .contact__icon {
    width: 14px;
    height: 14px;
    flex: none;
  }
  .back-mark {
    position: absolute;
    right: 34px;
    top: 150px;
    display: flex;
    align-items: center;
    gap: 14px;
  }
  .back-mark__dot {
    width: 18px;
    height: 18px;
    border-radius: 50%;
    background: var(--rose);
  }
  .back-mark__name {
    font-family: "Advent Pro", sans-serif;
    font-weight: 500;
    font-size: 72px;
    color: var(--rose);
  }
</style>
</head>
<body>
<main class="canvas">

  <section class="card card--front" aria-label="Card front">
    <div class="front-mark">
      <span class="front-mark__dot"></span>
      <span class="front-mark__name">Glimora</span>
    </div>
  </section>

  <section class="card card--back" aria-label="Card back">
    <div class="back-wordmark">Glimora</div>

    <div class="contact">
      <p class="contact__name">Maya Lorne</p>
      <p class="contact__address">123, Street Number, City Name,<br>Country - 123456</p>
      <ul class="contact__list">
        <li class="contact__item">
          <svg class="contact__icon" viewBox="0 0 16 16" fill="none" stroke="#8ccfc6" stroke-width="1.4">
            <path d="M4 1.5l2.3 3-1.4 1.6c.8 1.8 2.2 3.2 4 4l1.6-1.4 3 2.3-1.3 2.4C6.7 13.2 2.8 9.3 1.6 3z"/>
          </svg>
          00 111 222 333
        </li>
        <li class="contact__item">
          <svg class="contact__icon" viewBox="0 0 16 16" fill="none" stroke="#8ccfc6" stroke-width="1.4">
            <path d="M6.5 9.5l3-3"/>
            <path d="M7.5 4.5l1.5-1.5a2.8 2.8 0 014 4l-1.5 1.5"/>
            <path d="M8.5 11.5L7 13a2.8 2.8 0 01-4-4l1.5-1.5"/>
          </svg>
          www.glimora-example.com
        </li>
        <li class="contact__item">
          <svg class="contact__icon" viewBox="0 0 16 16" fill="none" stroke="#8ccfc6" stroke-width="1.4">
            <rect x="1.5" y="3.5" width="13" height="9"/>
            <path d="M1.5 3.5l6.5 5 6.5-5"/>
          </svg>
          yourname@glimora-example.com
        </li>
      </ul>
    </div>

    <div class="back-mark">
      <span class="back-mark__dot"></span>
      <span class="back-mark__name">Glimora</span>
    </div>
  </section>

</main>
</body>
</html>
```